Web design

We need the design for the logo and website for a women fashion website. No coding required. The colors used should be neutral (maybe with a light touch of color), the style should be modern, slightly luxurious, not too crowded. The target market is young professionals who love trendy clothes.
Updates

Need extra days to review

Target Market(s)

Young professionals

Industry/Entity Type

Apparel

Number of Pages Required

5+ page

Font styles to use
Sans Serif
Other font styles liked:
• Montserrat, Engravers Gothic, Benton Sans, gotham-book

Colors

Designer to choose colors to be used in the design.

```html
<!DOCTYPE html>
<html lang="en">
<head>
<meta charset="utf-8">
<title>VELLE – Finibus Bonorum</title>
<link href="https://fonts.googleapis.com/css2?family=Montserrat:wght@400;500;600&family=Inter:wght@400;500;600&display=swap" rel="stylesheet">
<style>
:root{
  --ink:#111111;
  --text:#333333;
  --muted:#7a7a7a;
  --line:#e4e4e4;
  --sale:#f0473a;
  --green:#3fb950;
  --sand:#dcc7b0;
  --foot:#f4f2f0;
  --brand:#1f1d33;
  --white:#ffffff;
}
*{margin:0;padding:0;box-sizing:border-box}
html,body{width:699px;height:1200px;overflow:hidden;background:var(--white)}
body{position:relative;font-family:'Montserrat',sans-serif;color:var(--text)}
.abs{position:absolute}
.ui{font-family:'Inter',sans-serif}

/* header */
.header{left:0;top:0;width:699px;height:44px;border-bottom:1px solid var(--line)}
.nav{left:58px;top:16px;display:flex;gap:17px;font-size:8px;color:var(--ink)}
.nav .sale{color:var(--sale)}
.wordmark{color:var(--brand);font-weight:500;letter-spacing:1px;white-space:nowrap}
.header .wordmark{left:0;width:699px;top:11px;text-align:center;font-size:18px;line-height:22px}
.tools{left:535px;top:14px;display:flex;align-items:center;gap:9px;font-size:7px;color:var(--ink)}
.badge{position:absolute;right:-4px;bottom:-3px;width:7px;height:7px;border-radius:50%;background:#e2a917;color:#fff;font-size:5px;text-align:center;line-height:7px}

/* gallery */
.thumb{left:58px;width:55px;height:60px;background:linear-gradient(#e6e3e3,#d2bfb1)}
.hero{left:118px;top:63px;width:304px;height:257px;background:linear-gradient(90deg,#e3e1e2,#d8c8bc 30%,#eceaea 49%,#e8e6e7 51%,#d9c6b8 70%,#ecebeb)}

/* product info */
.title{left:439px;top:70px;font-size:16.5px;font-weight:500;color:var(--ink)}
.price{left:441px;top:97px;font-size:7.5px;color:var(--ink);display:flex;align-items:center;gap:3px}
.price s{color:var(--muted)}
.save{margin-left:5px;border:1px solid #e2a917;color:#c9960f;font-size:5px;padding:2px 4px}
.stock{left:441px;top:114px;font-size:8px;color:var(--green);display:flex;align-items:center;gap:3px}
.divider{left:441px;top:131px;width:198px;height:1px;background:var(--line)}
.label-colours{left:441px;top:149px;font-size:7px;color:var(--muted)}
.swatch{top:163px;width:45px;height:63px}
.sizes{left:445px;top:234px;display:flex;gap:15px;font-size:6.5px;color:var(--ink)}
.sizes .off{color:var(--muted)}
.sizes .on{border-bottom:1px solid var(--ink);padding-bottom:1px}
.guide{left:441px;top:251px;font-size:7px;color:var(--muted);text-decoration:underline}
.cart-btn{left:440px;top:275px;width:157px;height:35px;background:var(--ink);color:#fff;font-size:11.5px;display:flex;align-items:center;justify-content:center;letter-spacing:.3px}

/* description */
.desc-h{left:59px;top:344px;font-size:7.6px;color:var(--ink)}
.desc{left:59px;top:357px;font-size:8px;line-height:14.3px;white-space:nowrap}
.feat-h{left:59px;top:411px;font-size:7.6px;color:var(--ink)}
.feat{left:59px;top:424px;font-size:8px;line-height:14.3px;list-style:none}
.care{left:186px;top:425px;font-size:8px;line-height:14.3px}

/* related */
.related-h{left:0;top:516px;width:699px;text-align:center;font-size:16.5px;font-weight:500;color:#222}
.card{top:552px;width:138px}
.card .pic{width:138px;height:186px;position:relative}
.tag{position:absolute;right:6px;bottom:6px;background:#fff;color:var(--sale);font-size:5.5px;padding:2px 8px}
.card .row{display:flex;justify-content:space-between;align-items:center;margin-top:5px;font-size:9px;color:var(--ink)}
.card .sub{font-size:7.6px;color:var(--muted);margin-top:3px}
.card .buy{display:flex;justify-content:space-between;align-items:baseline;margin-top:5px}
.card .amt{font-size:9.5px;font-weight:600;color:var(--ink)}
.card .amt s{font-size:6px;color:var(--muted);font-weight:500;margin-left:2px}
.card .sz{font-size:6px;color:var(--ink);word-spacing:1px}
.card .sz span{color:var(--muted)}

/* newsletter */
.news{left:0;top:836px;width:699px;height:165px;background:var(--sand)}
.news h2{position:absolute;top:44px;width:100%;text-align:center;font-size:21px;font-weight:600;color:var(--ink)}
.news p{position:absolute;top:75px;width:100%;text-align:center;font-size:7.6px;color:var(--text)}
.news .form{position:absolute;left:216px;top:96px;width:268px;height:25px;display:flex;border:1px solid #555}
.news .field{flex:1;font-size:7.5px;color:#555;padding-left:9px;display:flex;align-items:center}
.news .submit{width:134px;background:var(--ink);color:#fff;font-size:7.5px;font-weight:600;display:flex;align-items:center;justify-content:center}

/* footer */
.footer{left:0;top:1001px;width:699px;height:199px;background:var(--foot)}
.footer .wordmark{position:absolute;left:58px;top:50px;font-size:30px;line-height:34px}
.fcol{top:1045px}
.fcol h3{font-size:9px;font-weight:600;color:var(--ink);letter-spacing:.5px;margin-bottom:9px}
.fcol li{list-style:none;font-size:8px;line-height:15.5px;color:var(--text)}
.mail{display:flex;align-items:center;gap:4px;font-size:8px;margin-bottom:14px}
.socials{display:flex;gap:3px;margin-top:-2px}
.socials span{width:19px;height:19px;border:1px solid #444;border-radius:50%;display:block}
.frule{left:65px;top:1158px;width:569px;height:1px;background:#d8d6d4}
.legal{left:0;top:1172px;width:699px;text-align:center;font-size:8px}
</style>
</head>
<body>

<header class="abs header">
  <nav class="abs nav ui">
    <span>Latest Arrivals</span>
    <span>Clothes ⌄</span>
    <span>VELLE Club</span>
    <span class="sale">On Sale</span>
  </nav>
  <div class="abs wordmark">VELLE</div>
  <div class="abs tools ui">
    <svg width="10" height="10" viewBox="0 0 10 10" fill="none" stroke="#111" stroke-width="1"><circle cx="4.3" cy="4.3" r="3.3"/><path d="M6.8 6.8 9.3 9.3"/></svg>
    <span style="margin-left:11px">ENG ⌄</span>
    <svg width="14" height="13" viewBox="0 0 14 13" fill="none" stroke="#111" stroke-width="1"><path d="M7 12 1.6 6.6A3.2 3.2 0 0 1 7 2.2a3.2 3.2 0 0 1 5.4 4.4Z"/></svg>
    <svg width="12" height="14" viewBox="0 0 12 14" fill="none" stroke="#111" stroke-width="1"><circle cx="6" cy="4" r="3"/><path d="M1 13.5a5 5 0 0 1 10 0"/></svg>
    <span style="position:relative"><svg width="12" height="14" viewBox="0 0 12 14" fill="none" stroke="#111" stroke-width="1"><rect x="1" y="4.5" width="10" height="9"/><path d="M3.5 4.5V3a2.5 2.5 0 0 1 5 0v1.5"/></svg><span class="badge">0</span></span>
  </div>
</header>

<div class="abs thumb" style="top:63px" role="img" aria-label="Model in knit dress, front view"></div>
<div class="abs thumb" style="top:128px" role="img" aria-label="Model in knit dress, three-quarter view"></div>
<div class="abs thumb" style="top:194px" role="img" aria-label="Close-up of knit dress"></div>
<div class="abs thumb" style="top:260px" role="img" aria-label="Knit dress hem and heels"></div>
<div class="abs hero" role="img" aria-label="Model wearing a beige off-shoulder knit top and skirt, front and back views"></div>

<h1 class="abs title">Finibus Bonorum</h1>
<div class="abs price"><s>$150.00</s> $110.00 <span class="save">Save $40</span></div>
<div class="abs stock">
  <svg width="8" height="8" viewBox="0 0 8 8" fill="none" stroke="currentColor" stroke-width=".8"><circle cx="4" cy="4" r="3.5"/><path d="M2.3 4.1 3.5 5.2 5.8 2.9"/></svg>
  In Stock
</div>
<div class="abs divider"></div>
<div class="abs label-colours ui">Other Colours</div>
<div class="abs swatch" style="left:442px;background:linear-gradient(#d9cfc4,#b88e72)" role="img" aria-label="White lace top option"></div>
<div class="abs swatch" style="left:493px;background:linear-gradient(#e8e4e2,#8c2a33 50%,#8a6a50)" role="img" aria-label="Burgundy blouse with print skirt option"></div>
<div class="abs swatch" style="left:544px;background:linear-gradient(#eae7e6,#d96a4e 50%,#c9553d)" role="img" aria-label="Orange floral dress option"></div>
<div class="abs sizes ui"><span class="off">XXS</span><span class="on">XS</span><span>SM</span><span class="off">L</span><span>XL</span></div>
<div class="abs guide ui">Size Guide</div>
<div class="abs cart-btn">ADD TO CART</div>

<div class="abs desc-h ui">Description</div>
<p class="abs desc">Lorem ipsum dolor sit amet, consectetur adipiscing elit, sed do eiusmod<br>tempor incididunt ut labore et dolore magna aua. Quis ipsum suspendisse<br>ultrices gravida. Risus commodo v</p>
<div class="abs feat-h ui">FEATURES:</div>
<ul class="abs feat"><li>Soft rib jersey</li><li>Ruched bralette crop top</li><li>V front neckline and hem</li><li>Fitted</li></ul>
<div class="abs care">FIT, FABRIC &amp; CARE:<br>Eden is 180cm and is wearing a size S<br>95% Polyester, 5% Spandex</div>

<h2 class="abs related-h">You May Also Like</h2>

<div class="abs card" style="left:59px">
  <div class="pic" style="background:linear-gradient(#cfcccd,#3a3230 55%,#2b2522)" role="img" aria-label="Model in black polka dot dress"><span class="tag">20%</span></div>
  <div class="row ui">Prodcut Name <svg width="8" height="7" viewBox="0 0 14 13" fill="none" stroke="#111" stroke-width="1.4"><path d="M7 12 1.6 6.6A3.2 3.2 0 0 1 7 2.2a3.2 3.2 0 0 1 5.4 4.4Z"/></svg></div>
  <div class="sub">Lorem ipsum dolor sit amet</div>
  <div class="buy ui"><span class="amt">$32.99<s>$41.99</s></span><span class="sz"><span>XL</span> L M <span>S</span> XS</span></div>
</div>
<div class="abs card" style="left:207px">
  <div class="pic" style="background:linear-gradient(#e0dfe0,#d8d6d6 40%,#c9b29e)" role="img" aria-label="Model in white dotted summer dress"></div>
  <div class="row ui">Prodcut Name <svg width="8" height="7" viewBox="0 0 14 13" fill="none" stroke="#111" stroke-width="1.4"><path d="M7 12 1.6 6.6A3.2 3.2 0 0 1 7 2.2a3.2 3.2 0 0 1 5.4 4.4Z"/></svg></div>
  <div class="sub">Lorem ipsum dolor sit amet</div>
  <div class="buy ui"><span class="amt">$32.99<s>$41.99</s></span><span class="sz"><span>XL</span> L M <span>S</span> XS</span></div>
</div>
<div class="abs card" style="left:355px">
  <div class="pic" style="background:linear-gradient(90deg,#f1f0f0,#8e1f27 45%,#7c1820 55%,#f2f1f1)" role="img" aria-label="Model in burgundy lace gown"></div>
  <div class="row ui">Prodcut Name <svg width="8" height="7" viewBox="0 0 14 13" fill="none" stroke="#111" stroke-width="1.4"><path d="M7 12 1.6 6.6A3.2 3.2 0 0 1 7 2.2a3.2 3.2 0 0 1 5.4 4.4Z"/></svg></div>
  <div class="sub">Lorem ipsum dolor sit amet</div>
  <div class="buy ui"><span class="amt">$32.99<s>$41.99</s></span><span class="sz"><span>XL</span> L M <span>S</span> XS</span></div>
</div>
<div class="abs card" style="left:503px">
  <div class="pic" style="background:linear-gradient(#c19f80,#a5836a)" role="img" aria-label="Model in camel blazer"><span class="tag">On Sale</span></div>
  <div class="row ui">Prodcut Name <svg width="8" height="7" viewBox="0 0 14 13" fill="none" stroke="#111" stroke-width="1.4"><path d="M7 12 1.6 6.6A3.2 3.2 0 0 1 7 2.2a3.2 3.2 0 0 1 5.4 4.4Z"/></svg></div>
  <div class="sub">Lorem ipsum dolor sit amet</div>
  <div class="buy ui"><span class="amt">$32.99<s>$41.99</s></span><span class="sz"><span>XL</span> L M <span>S</span> XS</span></div>
</div>

<section class="abs news">
  <h2>Sign For Newsletter</h2>
  <p>We only send you the good stuff (including $10 off your first order)</p>
  <div class="form ui"><span class="field">Email Address</span><span class="submit">SUBSCRIBE</span></div>
</section>

<footer class="abs footer">
  <div class="wordmark">VELLE</div>
</footer>
<div class="abs fcol" style="left:259px"><h3>HELP</h3><ul><li>Terms &amp; Conditions</li><li>Privacy Policy</li><li>Returns/exchanges</li><li>Delivery Information</li><li>FAQ</li></ul></div>
<div class="abs fcol" style="left:429px"><h3>SHOP</h3><ul><li>Tops</li><li>Bootoms</li><li>Intimates</li><li>Dresses</li><li>Swim</li></ul></div>
<div class="abs fcol" style="left:560px">
  <h3 style="margin-bottom:5px">CONTACT US</h3>
  <div class="mail"><svg width="9" height="6" viewBox="0 0 9 6"><rect width="9" height="6" fill="#333"/><path d="M0 0 4.5 3.5 9 0" fill="none" stroke="#fff" stroke-width=".7"/></svg>info@velle.com</div>
  <h3>FOLLOW US</h3>
  <div class="socials"><span></span><span></span><span></span><span></span></div>
</div>
<div class="abs frule"></div>
<div class="abs legal">Terms &amp; Conditions, Privacy Policy and @2021 followed by velle.</div>

</body>
</html>
```